Designer Instructions – Updated Referral Program Flyer

(Based on the mock-up in “Brief Layout and Instructions.pdf”)

OVERALL STYLE + LAYOUT

Maintain the same general layout, structure, and flow as the mock-up flyer (front and back).

This is an update of an older flyer, not a full redesign — keep the same sections, proportions, and overall visual feel, but with cleaner, more modern design improvements.

The final flyer should look clean, bold, professional, and high-impact, geared toward realtors, property managers, and contractors who refer work.

FRONT SIDE INSTRUCTIONS
1. Header Section

Remove the Rebuild Harbor Crest logo from the top banner.
(Shown on page 1 of the PDF)

2. Main Headline

Keep the same three-line structure:
EARN
UNLIMITED
CASH

Center it, maximize impact, and increase the font size of CASH so all three words match in importance.

Make the headline bold, clean, and the main focal point.

3. Cash Incentive Box

Keep the "$500 minimum OR 10% per referral" box, but upgrade the graphics to look sharper and more modern.

Ensure the wording matches exactly what’s in the mock-up.

4. Premier Partner Program Ribbon

Clean up and modernize the "PREMIER PARTNER PROGRAM" bar while keeping the same position and structure.

Ensure the checkmark badge remains crisp and professional.

5. Supporting Icons Section

Keep the four icons/benefit boxes (Guaranteed Payout, Free Evaluations, Affordable Solutions, Industry Leaders) in the same order.

Update the icons to cleaner, more modern styles — but maintain the same meanings.

Improve alignment and spacing for sharper visual consistency.

6. Remove Icons in Contact Area

At the bottom (“CALL TEXT OR BOOK ONLINE 858-471-6093 BrightlaneRenovate.com”), remove the phone and internet icons, as noted on page 2 of the PDF.

7. Replace All Images

I (Dorian) will provide all updated stock images separately via email.

Replace the flood/water-damage imagery and roof leak with the new images I send.

Keep image placement and proportions the same as the mock-up.

BACK SIDE INSTRUCTIONS
1. Header Image + “REFER / EARN” Section

Maintain the same large split-image layout (“The more you refer, the more you earn”).

Replace all background imagery with the new assets I will send.

Keep the CASH FLOW image section but modernize the type and spacing.

2. “HOW IT WORKS” Section

Preserve the three-column layout:

Refer Flood, Water & Mold Damage

We Take Care of Everything (evaluations/insurance)

Get Paid to Share

Update images, tighten spacing, and use modern iconography.

3. Remove Phone/Internet Icons

Same as the front side — remove small communication icons and keep only the text/number/URL.

4. Bottom Contact Bar

Keep the blue bar, same wording, same layout — just modernize the style if needed for clarity.

5. Replace All Back-Side Images

Again, I will email you the image assets.

Keep the layout EXACT — just update with higher-quality photos and improved design.

TEXT CONTENT (Keep as-is unless spacing adjustments needed)

All text shown in the PDF should remain exactly the same unless spacing or visual balance requires minor adjustments.
Example from page 3:

“REFER FLOOD, MOLD & CONSTRUCTION JOBS”

“We Schedule a Free Estimate. If Approved, You Get Paid.”

“Everybody Benefits From Referrals”

Everything stays, just refreshed and visually improved.

DESIGN GOALS

Flyer should look high-end and trustworthy, not salesy.

Consistent color theme: blues, whites, yellows, same palette as original.

Use bold, modern fonts with strong readability.

Ensure all headlines pop and all benefit boxes are clean, well-aligned, and evenly spaced.

The final result should feel like a premium referral program flyer for a top-tier restoration/remodel company.

FILES I WILL PROVIDE

I will send the designer:

All replacement stock photos

Any updated logos (if needed)

Original high-resolution version of the mock-up (if available)

Any additional icons preferred

Colors
0054AA
0677BA
7BADD7
CADEEF
E8F1F8

Requirements
Must have
• Designer Instructions – Updated Referral Program Flyer (Based on the mock-up in “Brief Layout and Instructions.pdf”) OVERALL STYLE + LAYOUT Maintain the same general layout, structure, and flow as the mock-up flyer (front and back). This is an update of an older flyer, not a full redesign — keep the same sections, proportions, and overall visual feel, but with cleaner, more modern design improvements. The final flyer should look clean, bold, professional, and high-impact, geared toward realtors, property managers, and contractors who refer work. FRONT SIDE INSTRUCTIONS 1. Header Section Remove the Rebuild Harbor Crest logo from the top banner. (Shown on page 1 of the PDF) 2. Main Headline Keep the same three-line structure: EARN UNLIMITED CASH Center it, maximize impact, and increase the font size of CASH so all three words match in importance. Make the headline bold, clean, and the main focal point. 3. Cash Incentive Box Keep the "$500 minimum OR 10% per referral" box, but upgrade the graphics to look sharper and more modern. Ensure the wording matches exactly what’s in the mock-up. 4. Premier Partner Program Ribbon Clean up and modernize the "PREMIER PARTNER PROGRAM" bar while keeping the same position and structure. Ensure the checkmark badge remains crisp and professional. 5. Supporting Icons Section Keep the four icons/benefit boxes (Guaranteed Payout, Free Evaluations, Affordable Solutions, Industry Leaders) in the same order. Update the icons to cleaner, more modern styles — but maintain the same meanings. Improve alignment and spacing for sharper visual consistency. 6. Remove Icons in Contact Area At the bottom (“CALL TEXT OR BOOK ONLINE 858-471-6093 BrightlaneRenovate.com”), remove the phone and internet icons, as noted on page 2 of the PDF. 7. Replace All Images I (Dorian) will provide all updated stock images separately via email. Replace the flood/water-damage imagery and roof leak with the new images I send. Keep image placement and proportions the same as the mock-up. BACK SIDE INSTRUCTIONS 1. Header Image + “REFER / EARN” Section Maintain the same large split-image layout (“The more you refer, the more you earn”). Replace all background imagery with the new assets I will send. Keep the CASH FLOW image section but modernize the type and spacing. 2. “HOW IT WORKS” Section Preserve the three-column layout: Refer Flood, Water & Mold Damage We Take Care of Everything (evaluations/insurance) Get Paid to Share Update images, tighten spacing, and use modern iconography. 3. Remove Phone/Internet Icons Same as the front side — remove small communication icons and keep only the text/number/URL. 4. Bottom Contact Bar Keep the blue bar, same wording, same layout — just modernize the style if needed for clarity. 5. Replace All Back-Side Images Again, I will email you the image assets. Keep the layout EXACT — just update with higher-quality photos and improved design. TEXT CONTENT (Keep as-is unless spacing adjustments needed) All text shown in the PDF should remain exactly the same unless spacing or visual balance requires minor adjustments. Example from page 3: “REFER FLOOD, MOLD & CONSTRUCTION JOBS” “We Schedule a Free Estimate. If Approved, You Get Paid.” “Everybody Benefits From Referrals” Everything stays, just refreshed and visually improved. DESIGN GOALS Flyer should look high-end and trustworthy, not salesy. Consistent color theme: blues, whites, yellows, same palette as original. Use bold, modern fonts with strong readability. Ensure all headlines pop and all benefit boxes are clean, well-aligned, and evenly spaced. The final result should feel like a premium referral program flyer for a top-tier restoration/remodel company. FILES I WILL PROVIDE I will send the designer: All replacement stock photos Any updated logos (if needed) Original high-resolution version of the mock-up (if available) Any additional icons preferred

```html
<!DOCTYPE html>
<html lang="en">
<head>
<meta charset="utf-8">
<title>Refer a Flood – Referral Flyer</title>
<link rel="stylesheet" href="https://fonts.googleapis.com/css2?family=Archivo+Black&family=Montserrat:wght@500;600;700;800&display=swap">
<style>
  :root {
    --sky-blue: #1b69a5;
    --deep-navy: #06263d;
    --ink-navy: #1d3178;
    --bar-navy: #17327a;
    --banner-yellow: #fcd702;
    --tile-blue: #15598f;
    --water-top: #1c6fc6;
    --water-bottom: #2a86d6;
    --white: #ffffff;
    --steel: #b9bcc2;
  }
  html, body {
    margin: 0;
    padding: 0;
    width: 1200px;
    height: 800px;
    overflow: hidden;
    background: var(--white);
  }
  .flyer {
    display: block;
    width: 1200px;
    height: 800px;
  }
  .headline-small { font-family: "Archivo Black", sans-serif; fill: var(--white); }
  .headline-big { font-family: "Archivo Black", sans-serif; }
  .section-title { font-family: "Montserrat", sans-serif; font-weight: 800; fill: var(--ink-navy); }
  .tile-letter { font-family: "Montserrat", sans-serif; font-weight: 800; fill: var(--white); font-size: 50px; }
  .tile { fill: var(--tile-blue); stroke: #0c3f68; stroke-width: 1.5; }
  .card-frame { fill: none; stroke: var(--ink-navy); stroke-width: 5; }
  .card-title { font-family: "Montserrat", sans-serif; font-weight: 800; font-size: 21px; fill: var(--ink-navy); }
  .card-body { font-family: "Montserrat", sans-serif; font-weight: 600; font-size: 18.5px; fill: var(--ink-navy); }
  .contact-label { font-family: "Montserrat", sans-serif; font-weight: 800; font-size: 27px; fill: var(--white); }
  .contact-label .light { font-weight: 500; }
  .contact-info { font-family: "Montserrat", sans-serif; font-weight: 700; font-size: 29px; fill: var(--white); }
</style>
</head>
<body>
<svg class="flyer" viewBox="0 0 1200 800" xmlns="http://www.w3.org/2000/svg">
  <defs>
    <linearGradient id="gold" x1="0" y1="0" x2="1" y2="1">
      <stop offset="0" stop-color="#f8ee3c"/>
      <stop offset="0.5" stop-color="#f7c52a"/>
      <stop offset="1" stop-color="#f2963f"/>
    </linearGradient>
    <linearGradient id="cash-tones" x1="0" y1="0" x2="1" y2="1">
      <stop offset="0" stop-color="#cfcbc6"/>
      <stop offset="0.5" stop-color="#e6e3de"/>
      <stop offset="1" stop-color="#9d9b97"/>
    </linearGradient>
    <linearGradient id="water" x1="0" y1="0" x2="0" y2="1">
      <stop offset="0" stop-color="var(--water-top)"/>
      <stop offset="1" stop-color="var(--water-bottom)"/>
    </linearGradient>
    <linearGradient id="caption-fill" x1="0" y1="0" x2="1" y2="0">
      <stop offset="0" stop-color="#aeb1b7"/>
      <stop offset="0.45" stop-color="#e9eaec"/>
      <stop offset="1" stop-color="#f7f7f8"/>
    </linearGradient>
    <linearGradient id="room-tones" x1="0" y1="0" x2="1" y2="1">
      <stop offset="0" stop-color="#d9d5cf"/>
      <stop offset="0.6" stop-color="#6fb0cf"/>
      <stop offset="1" stop-color="#3f8fb8"/>
    </linearGradient>
    <linearGradient id="house-tones" x1="0" y1="0" x2="0" y2="1">
      <stop offset="0" stop-color="#e6e4de"/>
      <stop offset="0.6" stop-color="#a9b49a"/>
      <stop offset="1" stop-color="#5d8a4a"/>
    </linearGradient>
    <linearGradient id="sky-tones" x1="0" y1="0" x2="1" y2="1">
      <stop offset="0" stop-color="#5d9ee0"/>
      <stop offset="0.5" stop-color="#dfeaf6"/>
      <stop offset="1" stop-color="#7db0e3"/>
    </linearGradient>
    <clipPath id="card-inner-1"><rect x="83" y="376" width="326" height="316" rx="26"/></clipPath>
    <clipPath id="card-inner-2"><rect x="441" y="376" width="326" height="316" rx="26"/></clipPath>
    <clipPath id="card-inner-3"><rect x="798" y="376" width="326" height="316" rx="26"/></clipPath>
  </defs>

  <!-- Header panel -->
  <g class="header">
    <rect class="header-sky" x="0" y="0" width="720" height="347" fill="var(--sky-blue)"/>
    <polygon class="header-shadow" points="108,46 628,86 700,290 150,290 108,258" fill="var(--deep-navy)"/>

    <g class="headline">
      <text class="headline-small" x="105" y="88" font-size="38" textLength="396" lengthAdjust="spacingAndGlyphs">THE MORE YOU</text>
      <text class="headline-big" x="104" y="144" font-size="88" fill="url(#gold)" textLength="398" lengthAdjust="spacingAndGlyphs">REFER</text>
      <text class="headline-small" x="105" y="175" font-size="38" textLength="396" lengthAdjust="spacingAndGlyphs">THE MORE YOU</text>
      <text class="headline-big" x="105" y="256" font-size="106" fill="url(#gold)" textLength="396" lengthAdjust="spacingAndGlyphs">EARN</text>
    </g>

    <polygon class="how-band" points="0,286 697,286 714,347 0,347" fill="var(--banner-yellow)"/>
    <text class="section-title" x="107" y="335" font-size="51" textLength="402" lengthAdjust="spacingAndGlyphs">HOW IT WORKS</text>
  </g>

  <!-- Cash image with lettered tiles -->
  <g class="cash-flow">
    <polygon class="divider" points="606,0 624,0 718,347 698,347" fill="var(--steel)"/>
    <polygon class="cash-photo" role="img" aria-label="Photo of scattered hundred-dollar bills" points="622,0 1200,0 1200,347 716,347" fill="url(#cash-tones)"/>

    <g class="tiles tiles-refer">
      <rect class="tile" x="726" y="90" width="63" height="66" rx="3"/>
      <rect class="tile" x="790" y="90" width="63" height="66" rx="3"/>
      <rect class="tile" x="854" y="90" width="63" height="66" rx="3"/>
      <rect class="tile" x="918" y="90" width="63" height="66" rx="3"/>
      <rect class="tile" x="982" y="90" width="63" height="66" rx="3"/>
      <text class="tile-letter" x="757.5" y="141" text-anchor="middle">R</text>
      <text class="tile-letter" x="821.5" y="141" text-anchor="middle">E</text>
      <text class="tile-letter" x="885.5" y="141" text-anchor="middle">F</text>
      <text class="tile-letter" x="949.5" y="141" text-anchor="middle">E</text>
      <text class="tile-letter" x="1013.5" y="141" text-anchor="middle">R</text>
    </g>
    <g class="tiles tiles-flood">
      <rect class="tile" x="700" y="177" width="64" height="67" rx="3"/>
      <rect class="tile" x="793" y="177" width="64" height="67" rx="3"/>
      <rect class="tile" x="858" y="177" width="64" height="67" rx="3"/>
      <rect class="tile" x="923" y="177" width="64" height="67" rx="3"/>
      <rect class="tile" x="988" y="177" width="64" height="67" rx="3"/>
      <rect class="tile" x="1053" y="177" width="64" height="67" rx="3"/>
      <text class="tile-letter" x="732" y="229" text-anchor="middle">A</text>
      <text class="tile-letter" x="825" y="229" text-anchor="middle">F</text>
      <text class="tile-letter" x="890" y="229" text-anchor="middle">L</text>
      <text class="tile-letter" x="955" y="229" text-anchor="middle">O</text>
      <text class="tile-letter" x="1020" y="229" text-anchor="middle">O</text>
      <text class="tile-letter" x="1085" y="229" text-anchor="middle">D</text>
    </g>
  </g>

  <!-- Steps section -->
  <rect class="steps-water" role="img" aria-label="Blue background with water droplets" x="0" y="347" width="1200" height="453" fill="url(#water)"/>

  <g class="step step-refer">
    <g clip-path="url(#card-inner-1)">
      <rect class="step-photo" role="img" aria-label="Photo of drying fans and dehumidifiers in a room" x="83" y="376" width="326" height="182" fill="url(#room-tones)"/>
      <rect class="step-caption" x="83" y="558" width="326" height="134" fill="url(#caption-fill)"/>
    </g>
    <rect class="card-frame" x="81" y="374" width="330" height="320" rx="28"/>
    <text class="card-title" x="246" y="591" text-anchor="middle" textLength="266" lengthAdjust="spacingAndGlyphs">REFER FLOOD, WATER</text>
    <text class="card-title" x="246" y="614" text-anchor="middle" textLength="244" lengthAdjust="spacingAndGlyphs">AND MOLD DAMAGE</text>
    <text class="card-body" x="246" y="642" text-anchor="middle" textLength="264" lengthAdjust="spacingAndGlyphs">Our Rapid 24/7 Response</text>
    <text class="card-body" x="246" y="663" text-anchor="middle" textLength="214" lengthAdjust="spacingAndGlyphs">Team Arrives Fast to</text>
    <text class="card-body" x="246" y="684" text-anchor="middle" textLength="186" lengthAdjust="spacingAndGlyphs">Stop the Damage</text>
  </g>

  <g class="step step-care">
    <g clip-path="url(#card-inner-2)">
      <rect class="step-photo" role="img" aria-label="Photo of an inspector holding a work estimate in front of a house" x="441" y="376" width="326" height="182" fill="url(#house-tones)"/>
      <rect class="step-caption" x="441" y="558" width="326" height="134" fill="url(#caption-fill)"/>
    </g>
    <rect class="card-frame" x="439" y="374" width="330" height="320" rx="28"/>
    <text class="card-title" x="604" y="591" text-anchor="middle" textLength="228" lengthAdjust="spacingAndGlyphs">WE TAKE CARE OF</text>
    <text class="card-title" x="604" y="614" text-anchor="middle" textLength="160" lengthAdjust="spacingAndGlyphs">EVERYTHING</text>
    <text class="card-body" x="604" y="642" text-anchor="middle" textLength="306" lengthAdjust="spacingAndGlyphs">Free Inspection and Estimates</text>
    <text class="card-body" x="604" y="663" text-anchor="middle" textLength="188" lengthAdjust="spacingAndGlyphs">Certified Repairs</text>
    <text class="card-body" x="604" y="684" text-anchor="middle" textLength="180" lengthAdjust="spacingAndGlyphs">100% Guarantee</text>
  </g>

  <g class="step step-paid">
    <g clip-path="url(#card-inner-3)">
      <rect class="step-photo" role="img" aria-label="Photo of a yellow road sign reading Get Paid to Share against a cloudy sky" x="798" y="376" width="326" height="183" fill="url(#sky-tones)"/>
      <rect class="step-caption" x="798" y="559" width="326" height="133" fill="url(#caption-fill)"/>
    </g>
    <rect class="card-frame" x="796" y="374" width="330" height="320" rx="28"/>
    <text class="card-title" x="961" y="590" text-anchor="middle" textLength="242" lengthAdjust="spacingAndGlyphs">GET PAID TO SHARE</text>
    <text class="card-body" x="961" y="620" text-anchor="middle" textLength="294" lengthAdjust="spacingAndGlyphs">You Get Paid and Your Client</text>
    <text class="card-body" x="961" y="648" text-anchor="middle" textLength="196" lengthAdjust="spacingAndGlyphs">Gets The Help They</text>
    <text class="card-body" x="961" y="676" text-anchor="middle" textLength="102" lengthAdjust="spacingAndGlyphs">Need Fast</text>
  </g>

  <!-- Contact bar -->
  <g class="contact">
    <polygon class="contact-bar" points="0,723 508,723 551,800 0,800" fill="var(--bar-navy)"/>
    <text class="contact-label" x="79" y="772" textLength="423" lengthAdjust="spacingAndGlyphs">CALL, TEXT <tspan class="light">OR</tspan> BOOK ONLINE</text>
    <text class="contact-info" x="536" y="773" textLength="591" lengthAdjust="spacingAndGlyphs">858·471·6093 • BrightlaneRenovate.com</text>
  </g>
</svg>
</body>
</html>
```